Employment Agency Website Design

We are working with an employment agency in California.

Some sites to use for content/competitors and inspiration:

https://www.pinecrestjobs.com/us/en
https://www.velmorusa.com
https://www.dravenworks.us
https://www.quillora.com/en
https://www.tomvalusa.com
https://www.fernstaffing.com

Thank you for taking the time to consider designing a website for us. We are web developers based in Stockton, CA, USA. Most of our projects go through the same process. Understanding this process may help you win a project with us. We custom-code all of our websites in-house. We don’t have any requirements as to what tools you use for your design, but we prefer Figma files. For any design that we label as four-stars, we send it to the client for review. The client picks the final design they want us to use. Once we complete this process, we will continue to show additional clients all the four-star sites and purchase them later. Your designs will have multiple chances to sell. For better chances of success, we ask that you follow these guidelines.

IMAGES:
If you use any images or icons in the design, we ask that you have a link to the asset so we can purchase the image/icon. Most of the designs we submit do not have the customer’s images on them unless they have some great images. Be creative; show us the feeling you are trying to portray with your image choices. Use any royalty-free site you choose. We subscribe to Adobe and mainly use their images, but we can purchase images outside of Adobe. PLEASE NOTE: we will not submit designs to clients with watermarks on the images.

FONTS:
We ask that you identify the fonts used in the design. This can be done in a message if you want. We typically use Google Fonts and Adobe Fonts.

CONTENT:
We're always open to different content and ideas. We often submit designs with stock images so the client can see our vision. We typically take pictures after the website launch to use their images with our vision. Lorem Ipsum is fine for paragraphs, but we ask that you write the headers in correct English. We want to be able to show the vision and identify the sections of the website.

INSPIRATION:
We typically add a couple of links in the brief of websites we like to help you get started in your design.

REVISIONS:
We do not often ask for revisions of the designs unless we see something in the design that may not appeal to the client. If there are slight changes that we want to make, we do that in the development process.

FEEDBACK:
We rarely give feedback on designs during the design process. We are working on many website projects and do not have the time to provide feedback. We usually respond if your request is well thought out and asks specific questions, but a note asking “feedback, please” usually goes unanswered.

```html
<!DOCTYPE html>
<html lang="en">
<head>
<meta charset="UTF-8">
<title>brightpath talent — Connecting Talent With Opportunity</title>
<link href="https://fonts.googleapis.com/css2?family=Poppins:wght@400;500;600;700&family=Roboto:wght@400;500;700&display=swap" rel="stylesheet">
<style>
:root{
  --red:#c41e2b;
  --red-dark:#a3141f;
  --black:#0b0b0b;
  --ink:#1c1c1c;
  --muted:#6b6b6b;
  --pink:#fbeef0;
  --pink-soft:#fdf4f5;
  --white:#ffffff;
}
*{margin:0;padding:0;box-sizing:border-box}
html,body{width:1200px;height:4850px;overflow:hidden}
body{position:relative;background:var(--white);font-family:"Roboto",sans-serif;color:var(--ink)}
.abs{position:absolute}
h2.section-title{font-family:"Poppins",sans-serif;font-weight:700;font-size:34px;color:var(--ink)}
h2.section-title span{color:var(--red);font-weight:500}
.btn{position:absolute;display:flex;align-items:center;justify-content:center;gap:8px;font-family:"Roboto",sans-serif;font-weight:700;font-size:13px;color:var(--white);text-transform:uppercase;letter-spacing:.2px}
.btn-red{background:var(--red-dark)}
.btn-dot{width:12px;height:12px;border-radius:50%;background:var(--white);display:inline-flex;align-items:center;justify-content:center}
.btn-dot::after{content:"";border-left:5px solid var(--red-dark);border-top:3px solid transparent;border-bottom:3px solid transparent;margin-left:2px}
p.body{font-size:12.5px;line-height:25px;color:var(--muted)}
.photo{position:absolute}

/* header */
.topbar{left:527px;top:0;width:673px;height:38px;background:var(--red);clip-path:polygon(20px 0,100% 0,100% 100%,0 100%);z-index:4}
.topbar .seek{position:absolute;top:0;height:38px;display:flex;align-items:center;gap:10px;color:var(--white);font-weight:700;font-size:13px}
.topbar .ico{width:22px;height:22px;border-radius:50%;background:var(--white)}
.brand{position:absolute;left:78px;top:0;width:230px;height:156px;background:var(--white);display:flex;flex-direction:column;align-items:center;justify-content:flex-end;padding-bottom:14px;border-radius:0 0 22px 22px;z-index:5}
.brand .mark{width:64px;height:64px;border-radius:6px;background:var(--red);margin-bottom:10px}
.brand .name{font-family:"Poppins",sans-serif;font-size:21px;font-weight:500;color:var(--ink);line-height:26px}
.brand .tag{font-size:9px;color:var(--muted)}
.nav{position:absolute;left:388px;top:70px;display:flex;gap:30px;font-size:13px;font-weight:500;color:var(--ink);z-index:4}
.login{left:973px;top:56px;width:114px;height:42px;background:var(--black);border:3px solid var(--red);z-index:4}

/* hero */
.hero{left:0;top:107px;width:1200px;height:593px;background:linear-gradient(180deg,#fbe6e9,#fdf3f4)}
.hero h1{position:absolute;left:0;width:1200px;text-align:center;font-family:"Poppins",sans-serif}
.stat{position:absolute;background:var(--white);box-shadow:0 4px 14px rgba(0,0,0,.12);display:flex;align-items:center;gap:10px;padding:0 18px;height:64px}
.stat .av{width:26px;height:26px;border-radius:50%;background:#b9a597;border:2px solid var(--white);margin-left:-10px}
.stat b{font-family:"Poppins",sans-serif;font-size:24px}
.stat small{font-size:12px;color:var(--muted);line-height:14px}
.tile{position:absolute;width:46px;height:46px;background:var(--white);box-shadow:0 3px 10px rgba(0,0,0,.1);display:flex;align-items:center;justify-content:center}

/* search band */
.search{left:0;top:700px;width:1200px;height:170px;background:var(--red)}
.field{position:absolute;background:var(--white);height:54px;display:flex;align-items:center;padding-left:16px;font-size:12px;color:#777}

/* footer */
.footer{left:0;top:4254px;width:1200px;height:596px;background:var(--black);color:var(--white)}
.fcol{position:absolute;top:283px}
.fcol h4{font-size:13.5px;font-weight:700;margin-bottom:26px}
.fcol li{list-style:none;font-size:12.5px;line-height:27.5px;color:#e6e6e6}
</style>
</head>
<body>

<!-- header -->
<div class="abs topbar">
  <div class="seek" style="left:70px"><span class="ico"></span>Are you a job seeker?</div>
  <div class="seek" style="left:290px"><span class="ico"></span>Are you an employer?</div>
  <div class="seek" style="left:532px"><span class="ico" style="width:26px;height:26px"></span></div>
</div>
<div class="brand">
  <div class="mark"></div>
  <div class="name">brightpath talent</div>
  <div class="tag">The future of work</div>
</div>
<nav class="nav">
  <span>Find Jobs ▾</span><span>Hire Talent ▾</span><span>Explore Consulting Solutions ▾</span><span>Discover Insights ▾</span>
</nav>
<div class="btn login"><span style="width:14px;height:14px;background:var(--white);border-radius:2px"></span>LOGIN</div>

<!-- hero -->
<section class="abs hero">
  <div class="photo" role="img" aria-label="Smiling woman in a yellow blouse working on a laptop" style="left:0;top:140px;width:320px;height:453px;border-radius:160px 160px 0 0;background:linear-gradient(180deg,#f0cbb0 0%,#e9b77a 40%,#e4a02f 75%,#cf8a1f 100%)"></div>
  <div class="photo" role="img" aria-label="Businessman in a navy suit holding a laptop" style="left:850px;top:170px;width:350px;height:423px;border-radius:170px 170px 0 0;background:linear-gradient(180deg,#e0c3b2 0%,#b79a8d 30%,#3a4868 60%,#222c44 100%)"></div>
  <div class="tile" style="left:232px;top:244px"><svg width="28" height="28"><circle cx="14" cy="14" r="11" fill="none" stroke="#c41e2b" stroke-width="2.5"/><circle cx="14" cy="12" r="4" fill="#c41e2b"/></svg></div>
  <div class="tile" style="left:852px;top:327px"><svg width="26" height="26"><circle cx="10" cy="8" r="5" fill="#c41e2b"/><rect x="2" y="15" width="22" height="9" rx="3" fill="#c41e2b"/></svg></div>
  <h1 style="top:160px;font-size:44px;font-weight:700;color:var(--ink)">Connecting Talent</h1>
  <div class="abs" style="left:519px;top:228px;width:162px;height:2px;background:var(--ink)"></div>
  <h1 style="top:237px;font-size:44px;font-weight:400;color:var(--red)">With Opportunity</h1>
  <div class="btn btn-red" style="left:418px;top:394px;width:173px;height:40px">Find Your Next Job</div>
  <div class="btn btn-red" style="left:607px;top:394px;width:174px;height:40px">Find Your Next Hire</div>
  <div class="stat" style="left:288px;top:500px;width:230px"><span style="display:flex;margin-left:10px"><i class="av"></i><i class="av"></i><i class="av"></i></span><b>3k</b><small>people<br>Connected</small></div>
  <div class="stat" style="left:903px;top:448px;width:236px"><span style="display:flex;margin-left:10px"><i class="av"></i><i class="av"></i><i class="av"></i></span><b>1k</b><small>people<br>get job</small></div>
</section>

<!-- search -->
<section class="abs search">
  <div class="field" style="left:179px;top:61px;width:373px">Search For job Titles,Skills or keywords</div>
  <div class="field" style="left:572px;top:61px;width:243px">City ,State or zip code</div>
  <div class="btn" style="left:837px;top:60px;width:185px;height:56px;background:var(--black);border:1px solid var(--white)">Search Jobs</div>
</section>

<!-- about -->
<div class="photo" role="img" aria-label="Large red hexagon emblem filled with office team photography" style="left:111px;top:942px;width:403px;height:452px;background:radial-gradient(circle at 40% 30%,#e0505b,#c41e2b 45%,#8e1420);clip-path:polygon(50% 0,100% 25%,100% 75%,50% 100%,0 75%,0 25%)"></div>
<h2 class="section-title abs" style="left:601px;top:946px">Get To <span>Know Us.</span></h2>
<p class="body abs" style="left:602px;top:1016px;width:482px">Velmor helps you get a rewarding job and stay relevant in the ever-changing world of work. We understand the importance of a job in your life and we want to help you find work that makes you feel good. And we'll help you continue to grow as your needs and ambitions change. That's what we're here for and what motivates us every day.</p>
<p class="body abs" style="left:602px;top:1161px;width:482px">We provide outsourcing, staffing, consulting and workforce solutions within the areas of engineering, accounting and finance, healthcare human resources, IT, legal, life sciences, manufacturing and logistics, office and administration and sales and marketing. We can't wait to tell you all about it.</p>
<div class="btn btn-red" style="left:599px;top:1303px;width:140px;height:42px">View More <span class="btn-dot"></span></div>

<!-- discover -->
<div class="abs" style="left:0;top:1440px;width:1200px;height:650px;background:var(--pink-soft);clip-path:polygon(0 12%,30% 0,100% 8%,100% 90%,60% 100%,0 92%)"></div>
<h2 class="section-title abs" style="left:111px;top:1576px;line-height:54px">Discover What<br>Feels <span>&nbsp;Good To You.</span></h2>
<p class="body abs" style="left:113px;top:1702px;width:482px">At Velmor, we know that you're much more than your job experience. You're a unique person. With dreams and ideals. Passions and preferences. Needs and expectations. And the more we know about you, the better we can find you the job that fits best.</p>
<p class="body abs" style="left:113px;top:1830px;width:482px">Show us who you are. We'll show you how to turn your potential into work that feels good. Today, tomorrow, and throughout your career.</p>
<div class="btn btn-red" style="left:113px;top:1916px;width:140px;height:42px">View More <span class="btn-dot"></span></div>
<div class="photo" role="img" aria-label="Two colleagues discussing work at a desk in a bright office" style="left:648px;top:1545px;width:437px;height:433px;background:linear-gradient(160deg,#eef1f2 0%,#cfd8dc 35%,#c9a68f 55%,#56708a 75%,#2f4257 100%)"></div>

<!-- how it works -->
<h2 class="section-title abs" style="left:0;top:2167px;width:1200px;text-align:center">How It <span>Works</span></h2>
<svg class="abs" style="left:187px;top:2256px" width="120" height="140"><polygon points="60,4 116,36 116,104 60,136 4,104 4,36" fill="#c41e2b"/><polygon points="60,26 96,47 96,93 60,114 24,93 24,47" fill="#fff"/><rect x="44" y="56" width="32" height="24" fill="none" stroke="#c41e2b" stroke-width="2"/></svg>
<svg class="abs" style="left:518px;top:2256px" width="120" height="140"><polygon points="60,4 116,36 116,104 60,136 4,104 4,36" fill="#111"/><polygon points="60,26 96,47 96,93 60,114 24,93 24,47" fill="#fff"/><circle cx="60" cy="66" r="6" fill="none" stroke="#c41e2b" stroke-width="2"/><circle cx="45" cy="70" r="5" fill="none" stroke="#c41e2b" stroke-width="2"/><circle cx="75" cy="70" r="5" fill="none" stroke="#c41e2b" stroke-width="2"/></svg>
<svg class="abs" style="left:848px;top:2256px" width="120" height="140"><polygon points="60,4 116,36 116,104 60,136 4,104 4,36" fill="#c41e2b"/><polygon points="60,26 96,47 96,93 60,114 24,93 24,47" fill="#fff"/><circle cx="60" cy="70" r="18" fill="none" stroke="#222" stroke-width="2"/><circle cx="60" cy="64" r="6" fill="none" stroke="#222" stroke-width="2"/></svg>
<div class="abs" style="left:147px;top:2414px;width:200px;text-align:center;font-size:15.5px;font-weight:500">Describe your need</div>
<div class="abs" style="left:458px;top:2414px;width:240px;text-align:center;font-size:15.5px;font-weight:500">View matching candidates</div>
<div class="abs" style="left:803px;top:2414px;width:210px;text-align:center;font-size:15.5px;font-weight:500;line-height:24px">Connect with a recruiter to consult and hire</div>

<!-- career -->
<div class="abs" style="left:0;top:2562px;width:1200px;height:641px;background:var(--pink-soft);clip-path:polygon(0 10%,70% 0,100% 6%,100% 94%,40% 100%,0 92%)"></div>
<h2 class="section-title abs" style="left:0;top:2634px;width:1200px;text-align:center">Move Your <span>Career Forward.</span></h2>
<div class="photo" role="img" aria-label="Smiling woman in glasses and orange top" style="left:109px;top:2756px;width:232px;height:315px;background:linear-gradient(180deg,#ece3dc 0%,#d9a88c 30%,#d0603f 55%,#c41e2b 85%)"></div>
<div class="photo" role="img" aria-label="Man in a suit reviewing his resume" style="left:358px;top:2732px;width:232px;height:311px;background:linear-gradient(180deg,#dad6d3 0%,#a9a4a6 30%,#5a4e57 55%,#c41e2b 85%)"></div>
<div class="photo" role="img" aria-label="Three smiling colleagues standing together" style="left:607px;top:2756px;width:229px;height:315px;background:linear-gradient(180deg,#e3ddd8 0%,#c9a693 30%,#b7846e 50%,#c41e2b 85%)"></div>
<div class="photo" role="img" aria-label="Cardboard box of office items being handed over" style="left:855px;top:2732px;width:230px;height:311px;background:linear-gradient(180deg,#cfd2d4 0%,#a9aeb2 30%,#b98a68 55%,#c41e2b 85%)"></div>
<div class="abs" style="left:136px;top:3006px;width:175px;color:#fff;font-size:14px;line-height:26px">Find The Jobs Thats Fits You</div>
<div class="abs" style="left:385px;top:2980px;color:#fff;font-size:14px">Build Your Resume</div>
<div class="abs" style="left:607px;top:2956px;width:229px;text-align:center;color:#fff;font-size:14px">Today's in-demand jobs.</div>
<div class="btn" style="left:649px;top:2994px;width:144px;height:40px;border:1.5px solid #fff">View More <span class="btn-dot" style="background:#fff"></span></div>
<div class="abs" style="left:855px;top:2980px;width:230px;text-align:center;color:#fff;font-size:14px">Get paid what you're worth</div>
<svg class="abs" style="left:47px;top:2872px" width="34" height="34"><circle cx="17" cy="17" r="16" fill="#eee"/><path d="M19 12l-5 5 5 5" stroke="#555" stroke-width="1.6" fill="none"/></svg>
<svg class="abs" style="left:1115px;top:2872px" width="34" height="34"><circle cx="17" cy="17" r="16" fill="#c41e2b"/><path d="M15 12l5 5-5 5" stroke="#fff" stroke-width="1.6" fill="none"/></svg>
<div class="btn btn-red" style="left:530px;top:3113px;width:140px;height:42px">View More <span class="btn-dot"></span></div>

<!-- stories -->
<h2 class="section-title abs" style="left:0;top:3311px;width:1200px;text-align:center">Explore <span>Success Stories</span></h2>
<div class="abs" style="left:228px;top:3410px;width:349px;height:141px;background:#fff;box-shadow:0 6px 16px rgba(0,0,0,.1)"></div>
<div class="abs" style="left:648px;top:3410px;width:350px;height:141px;background:#fff;box-shadow:0 6px 16px rgba(0,0,0,.1)"></div>
<div class="photo" role="img" aria-label="Portrait of a satisfied client" style="left:200px;top:3443px;width:72px;height:72px;border-radius:50%;border:3px solid #fff;background:linear-gradient(180deg,#d8c3b3,#9c7f6e 50%,#2f3a55)"></div>
<div class="photo" role="img" aria-label="Portrait of a satisfied client" style="left:620px;top:3443px;width:72px;height:72px;border-radius:50%;border:3px solid #fff;background:linear-gradient(180deg,#d8c3b3,#9c7f6e 50%,#2f3a55)"></div>
<p class="body abs" style="left:297px;top:3430px;width:250px;text-align:justify">"Anyone searching knows how hard it is to find a position that aligns with your goals. They connected me with the perfect job."</p>
<p class="body abs" style="left:717px;top:3430px;width:250px;text-align:justify">"Anyone searching knows how hard it is to find a position that aligns with your goals. They connected me with the perfect job."</p>
<svg class="abs" style="left:47px;top:3463px" width="34" height="34"><circle cx="17" cy="17" r="16" fill="#eee"/><path d="M19 12l-5 5 5 5" stroke="#555" stroke-width="1.6" fill="none"/></svg>
<svg class="abs" style="left:1115px;top:3463px" width="34" height="34"><circle cx="17" cy="17" r="16" fill="#c41e2b"/><path d="M15 12l5 5-5 5" stroke="#fff" stroke-width="1.6" fill="none"/></svg>

<!-- app -->
<h2 class="section-title abs" style="left:111px;top:3777px;line-height:46px">App Your Way <span>To A<br>New Job</span></h2>
<div class="abs" style="left:113px;top:3910px;font-size:15.5px;font-weight:500;line-height:63px">
  <div style="display:flex;align-items:center;gap:30px"><svg width="36" height="36"><circle cx="18" cy="18" r="17" fill="#fbe4e7"/><path d="M12 18l4 4 8-8" stroke="#c41e2b" stroke-width="2.4" fill="none"/></svg>Get instantly notified of job matches</div>
  <div style="display:flex;align-items:center;gap:30px"><svg width="36" height="36"><circle cx="18" cy="18" r="17" fill="#fbe4e7"/><path d="M12 18l4 4 8-8" stroke="#c41e2b" stroke-width="2.4" fill="none"/></svg>Filter searches by skills and preferences</div>
  <div style="display:flex;align-items:center;gap:30px"><svg width="36" height="36"><circle cx="18" cy="18" r="17" fill="#fbe4e7"/><path d="M12 18l4 4 8-8" stroke="#c41e2b" stroke-width="2.4" fill="none"/></svg>Apply in a tap and much more</div>
</div>
<div class="abs" style="left:113px;top:4107px;width:160px;height:50px;background:#000;border-radius:7px;color:#fff;display:flex;align-items:center;gap:10px;padding-left:14px"><span style="width:22px;height:22px;background:#fff;border-radius:50%"></span><span style="font-size:9px;line-height:13px">Download on the<br><b style="font-size:18px;font-weight:500">App Hub</b></span></div>
<div class="abs" style="left:292px;top:4107px;width:179px;height:50px;background:#000;border-radius:7px;color:#fff;display:flex;align-items:center;gap:10px;padding-left:14px"><span style="width:22px;height:22px;background:#fff"></span><span style="font-size:9px;line-height:13px">GET IT ON<br><b style="font-size:18px;font-weight:500">Droid Shelf</b></span></div>

<!-- footer -->
<section class="abs footer" style="clip-path:polygon(0 0,58% 8%,100% 0,100% 100%,0 100%)">
  <div class="abs" style="left:0;top:120px;width:1200px;display:flex;flex-direction:column;align-items:center">
    <div style="width:60px;height:60px;border-radius:6px;background:#fff;margin-bottom:12px"></div>
    <div style="font-family:Poppins,sans-serif;font-size:22px;font-weight:500">brightpath talent</div>
    <div style="font-size:9px;color:#bbb">The future of work</div>
  </div>
  <div class="fcol" style="left:121px"><h4>Services</h4><ul><li>Browse Jobs</li><li>Contract Talent</li><li>Permanent Talent</li><li>Consulting Solutions</li></ul></div>
  <div class="fcol" style="left:369px"><h4>Areas of Expertise</h4><ul><li>Finance &amp; Accounting</li><li>Technology</li><li>Marketing &amp; Creative</li><li>Administrative &amp; Customer Support</li><li>Legal</li></ul></div>
  <div class="fcol" style="left:720px"><h4>Resources &amp; Tools</h4><ul><li>Discover Insights</li><li>Invoice</li><li>Job Directory</li><li>Salary Guide</li><li>Time Reports</li><li>Contact Us</li></ul></div>
  <div class="fcol" style="left:951px"><h4>About</h4><ul><li>Leadership</li><li>Careers With Us</li><li>Locations</li><li>Investor Center</li><li>Press</li><li>Our Brands</li></ul></div>
  <div class="abs" style="left:537px;top:492px;display:flex;gap:20px"><span style="width:28px;height:28px;border-radius:50%;background:#fff"></span><span style="width:28px;height:28px;border-radius:50%;background:#fff"></span><span style="width:28px;height:28px;border-radius:50%;background:#fff"></span></div>
  <div class="abs" style="left:0;top:555px;width:1200px;text-align:center;font-size:12.5px">Copyright@2024 - All Rights Reserved by brightpath talent</div>
</section>

<!-- phone -->
<div class="abs" style="left:712px;top:3777px;width:377px;height:556px;background:#fff;border:10px solid #ececec;border-bottom:none;border-radius:46px 46px 0 0;box-shadow:0 0 30px rgba(0,0,0,.08);overflow:hidden">
  <div style="display:flex;justify-content:space-between;padding:18px 26px 0;font-size:13px;font-weight:700"><span>09:41</span><span>▮▮ ◔ ▭</span></div>
  <div style="margin:14px 28px 0;height:30px;border-radius:15px;background:#f1f1f1;font-size:11.5px;color:#444;display:flex;align-items:center;padding-left:44px">Job titles, skills or keywords</div>
  <div style="display:flex;flex-direction:column;align-items:center;margin-top:78px">
    <div style="width:70px;height:70px;border-radius:6px;background:var(--red);margin-bottom:10px"></div>
    <div style="font-family:Poppins,sans-serif;font-size:22px;font-weight:500">brightpath talent</div>
    <div style="font-size:8px;color:#999">The future of work</div>
  </div>
  <div style="margin:86px 18px 0;height:160px;border:3px solid #c9b6ea;border-radius:14px;padding:14px 24px;font-family:Poppins,sans-serif">
    <div style="font-size:9px;font-weight:600">New</div>
    <div style="font-size:14px;margin-top:4px">Staff Accountant</div>
    <div style="font-size:9px;color:#666">Permanent | ⊘</div>
    <div style="font-size:9.5px;line-height:13px;margin-top:8px">As a Staff Accountant, you'll be responsible for preparing journal entries, monthly and year-end closings, bank reconciliation, fixed asset mainte...</div>
    <div style="font-size:9px;margin-top:6px">⌖ San Francisco, CA</div>
  </div>
</div>

</body>
</html>
```